Vernac Law Business cards and stationary design project

We are looking for a stationary design for business cards (double sided), 8x10, 5x7, and legal and standard envelopes.

We would like the design to match the logo that we have already.
Color palate preferred is Teal, White, grey and any others that will look good for a professional law firm.

We would like this statement: "RELATIONSHIPS. RESPECT. RESULT" to be on the back of the business cards and maybe on the stationary if it looks good.

Please see link to website for more information: www.vernac-law.example

Target Market(s)

Potential clients that need Attorney services.

Industry/Entity Type

Law Firm

Contact Information for Business Card

We would like the front and back to be two different colors. Current business cards are teal front, grey back and are a vertical design. We are open to options with colors.

Font styles to use
Serif

Colors
33a6d7
33b8a4
b9b9b9
5c5c5c

Requirements
Must have
• Logo supplied needs to go on the card and stationary.
• Match website color palate, www.vernac-law.example
• Be professional and not too wordy.
• Criminal Law, Civil Litigation, Personal Injury, Restraining Orders need to be on the card.
Nice to have
• RELATIONSHIPS. RESPECT. RESULTS. on the back of the card.
Should not have
• Not be too busy/wordy or too flashy.

```html
<!DOCTYPE html>
<html lang="en">
<head>
<meta charset="utf-8">
<title>Vernac Law – Business Cards</title>
<link href="https://fonts.googleapis.com/css2?family=Lato:wght@400;700&display=swap" rel="stylesheet">
<style>
  :root {
    --teal: #13879a;
    --teal-dark: #0f7686;
    --paper: #ffffff;
    --paper-tint: #eefbfd;
    --backdrop: #ecebe8;
    --ink-light: #ffffff;
  }
  * { box-sizing: border-box; margin: 0; padding: 0; }
  html, body { width: 1200px; height: 900px; overflow: hidden; }
  body {
    background: var(--backdrop);
    font-family: "Lato", Arial, sans-serif;
    position: relative;
  }
  .card {
    position: absolute;
    width: 540px;
    height: 310px;
    overflow: hidden;
    box-shadow: 0 6px 18px rgba(0,0,0,0.18);
    display: flex;
    flex-direction: column;
  }
  .card--back { left: 60px; top: 150px; }
  .card--front { left: 600px; top: 440px; }

  .card__head {
    height: 50%;
    display: flex;
    align-items: center;
    justify-content: center;
    gap: 14px;
  }
  .card--back .card__head { background: var(--paper-tint); }
  .card--front .card__head { background: var(--paper); }

  .brand-mark {
    width: 34px; height: 34px;
    background: var(--teal);
  }
  .brand-name {
    font-family: "Lato", Arial, sans-serif;
    font-weight: 400;
    font-size: 40px;
    letter-spacing: 3px;
    text-transform: uppercase;
    color: var(--teal);
  }

  .card__band {
    flex: 1;
    background: var(--teal);
    color: var(--ink-light);
  }

  .card--back .card__band {
    display: flex;
    flex-direction: column;
    align-items: center;
    justify-content: center;
    text-align: center;
    gap: 4px;
  }
  .practice-areas { font-size: 14px; line-height: 1.45; }
  .tagline {
    margin-top: 10px;
    font-size: 14px;
    font-weight: 700;
    letter-spacing: 0.5px;
  }

  .card--front .card__band {
    display: flex;
    align-items: center;
    justify-content: space-between;
    padding: 0 40px 0 50px;
  }
  .person { text-align: right; }
  .person__name { font-size: 24px; font-weight: 700; }
  .person__role { font-size: 17px; margin-top: 2px; }
  .person__address { font-size: 17px; margin-top: 14px; line-height: 1.3; }

  .contact-list { list-style: none; }
  .contact-list li {
    display: flex;
    align-items: center;
    gap: 8px;
    font-size: 15px;
    line-height: 1.45;
  }
  .contact-icon { width: 16px; height: 16px; flex: none; }
</style>
</head>
<body>

  <section class="card card--back">
    <header class="card__head">
      <span class="brand-mark"></span>
      <span class="brand-name">Vernac Law</span>
    </header>
    <div class="card__band">
      <p class="practice-areas">Practice areas, Criminal Law<br>Civil Litigation/Personal Injury, Restraining Orders</p>
      <p class="tagline">RELATIONSHIPS. RESPECT. RESULT</p>
    </div>
  </section>

  <section class="card card--front">
    <header class="card__head">
      <span class="brand-mark"></span>
      <span class="brand-name">Vernac Law</span>
    </header>
    <div class="card__band">
      <div class="person">
        <p class="person__name">John Smith</p>
        <p class="person__role">Managing Director</p>
        <p class="person__address">1234, Address GoesHere<br>Country, 12345</p>
      </div>
      <ul class="contact-list">
        <li>
          <svg class="contact-icon" viewBox="0 0 16 16"><rect width="16" height="16" rx="2" fill="#fff"/><path d="M4 4h3l1 3-2 1a6 6 0 0 0 2 2l1-2 3 1v3h-2A8 8 0 0 1 4 6z" fill="#13879a"/></svg>
          123-456-7890
        </li>
        <li>
          <svg class="contact-icon" viewBox="0 0 16 16"><rect width="16" height="16" rx="2" fill="#fff"/><rect x="4" y="3" width="8" height="4" fill="#13879a"/><rect x="3" y="7" width="10" height="6" fill="#13879a"/><rect x="5" y="9" width="6" height="1.5" fill="#fff"/></svg>
          123-456-7890
        </li>
        <li>
          <svg class="contact-icon" viewBox="0 0 16 16"><rect width="16" height="16" rx="2" fill="#fff"/><rect x="3" y="4.5" width="10" height="7" fill="#13879a"/><path d="M3 4.5l5 4 5-4" stroke="#fff" stroke-width="1.2" fill="none"/></svg>
          info@youremail.com
        </li>
        <li>
          <svg class="contact-icon" viewBox="0 0 16 16"><rect width="16" height="16" rx="2" fill="#fff"/><path d="M6.5 9.5l3-3M7 5l1-1a2 2 0 0 1 3 3l-1 1M9 11l-1 1a2 2 0 0 1-3-3l1-1" stroke="#13879a" stroke-width="1.5" fill="none" stroke-linecap="round"/></svg>
          www.yourweb.com
        </li>
      </ul>
    </div>
  </section>

</body>
</html>
```